Designer Instructions – Updated Referral Program Flyer

(Based on the mock-up in “Brief Layout and Instructions.pdf”)

OVERALL STYLE + LAYOUT

Maintain the same general layout, structure, and flow as the mock-up flyer (front and back).

This is an update of an older flyer, not a full redesign — keep the same sections, proportions, and overall visual feel, but with cleaner, more modern design improvements.

The final flyer should look clean, bold, professional, and high-impact, geared toward realtors, property managers, and contractors who refer work.

FRONT SIDE INSTRUCTIONS
1. Header Section

Remove the Rebuild Harbor Crest logo from the top banner.
(Shown on page 1 of the PDF)

2. Main Headline

Keep the same three-line structure:
EARN
UNLIMITED
CASH

Center it, maximize impact, and increase the font size of CASH so all three words match in importance.

Make the headline bold, clean, and the main focal point.

3. Cash Incentive Box

Keep the "$500 minimum OR 10% per referral" box, but upgrade the graphics to look sharper and more modern.

Ensure the wording matches exactly what’s in the mock-up.

4. Premier Partner Program Ribbon

Clean up and modernize the "PREMIER PARTNER PROGRAM" bar while keeping the same position and structure.

Ensure the checkmark badge remains crisp and professional.

5. Supporting Icons Section

Keep the four icons/benefit boxes (Guaranteed Payout, Free Evaluations, Affordable Solutions, Industry Leaders) in the same order.

Update the icons to cleaner, more modern styles — but maintain the same meanings.

Improve alignment and spacing for sharper visual consistency.

6. Remove Icons in Contact Area

At the bottom (“CALL TEXT OR BOOK ONLINE 858-471-6093 BrightlaneRenovate.com”), remove the phone and internet icons, as noted on page 2 of the PDF.

7. Replace All Images

I (Dorian) will provide all updated stock images separately via email.

Replace the flood/water-damage imagery and roof leak with the new images I send.

Keep image placement and proportions the same as the mock-up.

BACK SIDE INSTRUCTIONS
1. Header Image + “REFER / EARN” Section

Maintain the same large split-image layout (“The more you refer, the more you earn”).

Replace all background imagery with the new assets I will send.

Keep the CASH FLOW image section but modernize the type and spacing.

2. “HOW IT WORKS” Section

Preserve the three-column layout:

Refer Flood, Water & Mold Damage

We Take Care of Everything (evaluations/insurance)

Get Paid to Share

Update images, tighten spacing, and use modern iconography.

3. Remove Phone/Internet Icons

Same as the front side — remove small communication icons and keep only the text/number/URL.

4. Bottom Contact Bar

Keep the blue bar, same wording, same layout — just modernize the style if needed for clarity.

5. Replace All Back-Side Images

Again, I will email you the image assets.

Keep the layout EXACT — just update with higher-quality photos and improved design.

TEXT CONTENT (Keep as-is unless spacing adjustments needed)

All text shown in the PDF should remain exactly the same unless spacing or visual balance requires minor adjustments.
Example from page 3:

“REFER FLOOD, MOLD & CONSTRUCTION JOBS”

“We Schedule a Free Estimate. If Approved, You Get Paid.”

“Everybody Benefits From Referrals”

Everything stays, just refreshed and visually improved.

DESIGN GOALS

Flyer should look high-end and trustworthy, not salesy.

Consistent color theme: blues, whites, yellows, same palette as original.

Use bold, modern fonts with strong readability.

Ensure all headlines pop and all benefit boxes are clean, well-aligned, and evenly spaced.

The final result should feel like a premium referral program flyer for a top-tier restoration/remodel company.

FILES I WILL PROVIDE

I will send the designer:

All replacement stock photos

Any updated logos (if needed)

Original high-resolution version of the mock-up (if available)

Any additional icons preferred

Colors
0054AA
0677BA
7BADD7
CADEEF
E8F1F8

Requirements
Must have
• Designer Instructions – Updated Referral Program Flyer (Based on the mock-up in “Brief Layout and Instructions.pdf”) OVERALL STYLE + LAYOUT Maintain the same general layout, structure, and flow as the mock-up flyer (front and back). This is an update of an older flyer, not a full redesign — keep the same sections, proportions, and overall visual feel, but with cleaner, more modern design improvements. The final flyer should look clean, bold, professional, and high-impact, geared toward realtors, property managers, and contractors who refer work. FRONT SIDE INSTRUCTIONS 1. Header Section Remove the Rebuild Harbor Crest logo from the top banner. (Shown on page 1 of the PDF) 2. Main Headline Keep the same three-line structure: EARN UNLIMITED CASH Center it, maximize impact, and increase the font size of CASH so all three words match in importance. Make the headline bold, clean, and the main focal point. 3. Cash Incentive Box Keep the "$500 minimum OR 10% per referral" box, but upgrade the graphics to look sharper and more modern. Ensure the wording matches exactly what’s in the mock-up. 4. Premier Partner Program Ribbon Clean up and modernize the "PREMIER PARTNER PROGRAM" bar while keeping the same position and structure. Ensure the checkmark badge remains crisp and professional. 5. Supporting Icons Section Keep the four icons/benefit boxes (Guaranteed Payout, Free Evaluations, Affordable Solutions, Industry Leaders) in the same order. Update the icons to cleaner, more modern styles — but maintain the same meanings. Improve alignment and spacing for sharper visual consistency. 6. Remove Icons in Contact Area At the bottom (“CALL TEXT OR BOOK ONLINE 858-471-6093 BrightlaneRenovate.com”), remove the phone and internet icons, as noted on page 2 of the PDF. 7. Replace All Images I (Dorian) will provide all updated stock images separately via email. Replace the flood/water-damage imagery and roof leak with the new images I send. Keep image placement and proportions the same as the mock-up. BACK SIDE INSTRUCTIONS 1. Header Image + “REFER / EARN” Section Maintain the same large split-image layout (“The more you refer, the more you earn”). Replace all background imagery with the new assets I will send. Keep the CASH FLOW image section but modernize the type and spacing. 2. “HOW IT WORKS” Section Preserve the three-column layout: Refer Flood, Water & Mold Damage We Take Care of Everything (evaluations/insurance) Get Paid to Share Update images, tighten spacing, and use modern iconography. 3. Remove Phone/Internet Icons Same as the front side — remove small communication icons and keep only the text/number/URL. 4. Bottom Contact Bar Keep the blue bar, same wording, same layout — just modernize the style if needed for clarity. 5. Replace All Back-Side Images Again, I will email you the image assets. Keep the layout EXACT — just update with higher-quality photos and improved design. TEXT CONTENT (Keep as-is unless spacing adjustments needed) All text shown in the PDF should remain exactly the same unless spacing or visual balance requires minor adjustments. Example from page 3: “REFER FLOOD, MOLD & CONSTRUCTION JOBS” “We Schedule a Free Estimate. If Approved, You Get Paid.” “Everybody Benefits From Referrals” Everything stays, just refreshed and visually improved. DESIGN GOALS Flyer should look high-end and trustworthy, not salesy. Consistent color theme: blues, whites, yellows, same palette as original. Use bold, modern fonts with strong readability. Ensure all headlines pop and all benefit boxes are clean, well-aligned, and evenly spaced. The final result should feel like a premium referral program flyer for a top-tier restoration/remodel company. FILES I WILL PROVIDE I will send the designer: All replacement stock photos Any updated logos (if needed) Original high-resolution version of the mock-up (if available) Any additional icons preferred

```html
<!DOCTYPE html>
<html lang="en">
<head>
<meta charset="utf-8">
<title>Partner Referral Program Flyer</title>
<link rel="stylesheet" href="https://fonts.googleapis.com/css2?family=Bebas+Neue&family=Montserrat:wght@500;600;700;800;900&display=swap">
<style>
:root{
  --navy:#062b6b;
  --navy-deep:#05234f;
  --panel-blue:#0f6aa3;
  --shadow-blue:#03283f;
  --red:#dc3d35;
  --yellow:#fcd116;
  --gold:#f7a823;
  --cream:#ffe3a3;
  --white:#ffffff;
  --ink:#111111;
  --stage:#dcdcdc;
}
*{margin:0;padding:0;box-sizing:border-box}
html,body{width:924px;height:1200px;overflow:hidden;background:var(--stage);font-family:"Montserrat",sans-serif}
.flyer{position:absolute;left:113px;width:697px;height:450px;background:var(--white);overflow:hidden;box-shadow:0 10px 22px rgba(0,0,0,.18)}
.flyer--front{top:110px}
.flyer--back{top:641px}
.abs{position:absolute}

/* FRONT */
.hero{left:0;top:0;width:697px;height:199px;background:radial-gradient(ellipse 60% 90% at 50% 15%,#0d4fb0 0%,var(--navy) 60%);text-align:center}
.hero__title{position:absolute;left:0;right:0;top:10px;color:var(--white);font-weight:900;font-size:70px;line-height:55px;letter-spacing:-2px;text-shadow:0 3px 6px rgba(0,0,0,.35)}
.incentive{left:0;top:203px;width:343px;height:50px;background:var(--navy);color:var(--white)}
.incentive__amount{position:absolute;top:4px;text-align:center;line-height:1}
.incentive__amount b{display:block;color:var(--yellow);font-weight:800;font-size:24px}
.incentive__amount span{display:block;font-weight:600;font-size:16px;margin-top:1px}
.incentive__or{position:absolute;left:145px;top:12px;font-size:25px;font-weight:600}
.partner-bar{left:348px;top:203px;width:349px;height:50px;background:var(--red)}
.partner-bar__text{position:absolute;left:60px;right:0;top:5px;text-align:center;line-height:1}
.partner-bar__text small{display:block;color:var(--white);font-weight:800;font-size:16px}
.partner-bar__text strong{display:block;color:var(--yellow);font-weight:900;font-size:21px;margin-top:2px}
.yellow-rule{left:0;width:697px;height:5px;background:var(--yellow)}
.tab{background:var(--yellow);clip-path:polygon(0 0,100% 0,96% 100%,4% 100%);text-align:center;color:var(--ink);font-weight:800}
.tab--wins{left:175px;top:256px;width:349px;height:26px;font-size:15px;line-height:26px}
.benefit{top:293px;width:150px;text-align:center;color:var(--ink)}
.benefit__icon{display:block;margin:0 auto;width:37px;height:37px}
.benefit__title{margin-top:3px;color:var(--navy);font-weight:800;font-size:12px;line-height:13.5px}
.benefit__text{margin-top:2px;font-weight:500;font-size:10.5px;line-height:12.5px}
.divider{top:303px;width:1px;height:80px;background:#444}
.contact{left:0;width:697px}
.contact__call{left:0;top:0;width:350px;height:100%;background:var(--yellow);clip-path:polygon(0 0,94% 0,100% 50%,94% 100%,0 100%)}
.contact__call-text{position:absolute;left:28px;top:0;height:100%;display:flex;align-items:center;font-weight:800;font-size:19px;color:var(--ink)}
.contact__info{left:330px;top:0;right:0;height:100%;background:var(--navy);clip-path:polygon(4% 0,100% 0,100% 100%,4% 100%,9% 50%)}
.contact__phone,.contact__web{position:absolute;top:0;height:100%;display:flex;align-items:center;color:var(--white);font-weight:700;font-size:13px}
.contact__phone{left:362px}
.contact__web{left:470px}
.contact__sep{position:absolute;left:461px;width:1.5px;background:var(--yellow)}

/* BACK */
.refer-panel{left:0;top:0;width:266px;height:198px;background:var(--panel-blue)}
.refer-panel svg{position:absolute;left:0;top:0}
.refer-title{position:absolute;left:65px;top:0;width:140px;height:198px;font-family:"Bebas Neue",sans-serif}
.refer-title span{position:absolute;left:0;line-height:1;white-space:nowrap;letter-spacing:-.5px}
.refer-title .lead{color:var(--white);font-size:34px}
.refer-title .big{background:linear-gradient(180deg,var(--yellow) 30%,var(--gold) 100%);-webkit-background-clip:text;background-clip:text;color:transparent}
.refer-title .refer{top:32px;font-size:78px}
.refer-title .earn{top:116px;font-size:90px}
.cashflow-photo{left:270px;top:0;width:427px;height:198px;background:linear-gradient(135deg,#cfd3cc 0%,#9aa39a 45%,#e4e6e0 70%,#7f8a84 100%)}
.tab--how{left:221px;top:177px;width:239px;height:26px;font-size:18px;line-height:27px;clip-path:polygon(8% 0,92% 0,100% 100%,0 100%)}
.red-band{left:0;top:350px;width:697px;height:50px;background:var(--red)}
.red-band__text{position:absolute;left:0;right:0;bottom:4px;text-align:center;color:var(--cream);font-weight:800;font-size:18px}
.step{top:213px;width:206px;height:156px;background:var(--white);border:2px solid var(--navy);border-radius:12px;overflow:hidden;text-align:center}
.step__photo{position:absolute;left:2px;top:2px;right:2px;height:86px;border-radius:9px 9px 0 0}
.step__photo--fans{background:linear-gradient(160deg,#c9c6bd,#3c86a8 60%,#8c8a84)}
.step__photo--estimate{background:linear-gradient(160deg,#e9e9e4,#8aa06a 55%,#5c87b6)}
.step__photo--sign{background:linear-gradient(160deg,#4d86c8,#dfe8f2 55%,#f5d10f)}
.step__label{position:absolute;left:2px;right:2px;top:88px;height:32px;background:var(--navy);color:var(--white);font-weight:700;font-size:12px;line-height:11.5px;display:flex;align-items:center;justify-content:center}
.step__text{position:absolute;left:2px;right:2px;top:122px;font-weight:500;font-size:10px;line-height:12px;color:var(--ink)}
</style>
</head>
<body>

<section class="flyer flyer--front">
  <header class="hero abs">
    <h1 class="hero__title">EARN<br>UNLIMITED<br>CASH</h1>
  </header>

  <div class="incentive abs">
    <div class="incentive__amount" style="left:40px;width:86px"><b>$500</b><span>Minimum</span></div>
    <div class="incentive__or">OR</div>
    <div class="incentive__amount" style="left:210px;width:105px"><b>10%</b><span>Per Referral</span></div>
  </div>

  <div class="partner-bar abs">
    <svg class="abs" style="left:14px;top:7px" width="40" height="38" viewBox="0 0 40 38" aria-hidden="true">
      <path d="M20 2 L36 7 V18 C36 27 29 33 20 36 C11 33 4 27 4 18 V7 Z" fill="none" stroke="var(--yellow)" stroke-width="4"/>
      <path d="M11 18 L18 25 L34 6" fill="none" stroke="var(--yellow)" stroke-width="5" stroke-linecap="round" stroke-linejoin="round"/>
    </svg>
    <div class="partner-bar__text"><small>PREMIER</small><strong>PARTNER PROGRAM</strong></div>
  </div>

  <div class="yellow-rule abs" style="top:256px"></div>
  <div class="tab tab--wins abs">PARTNER WITH US &amp; EVERYBODY WINS !</div>

  <div class="benefit abs" style="left:31px">
    <svg class="benefit__icon" viewBox="0 0 40 40" aria-hidden="true"><circle cx="20" cy="20" r="18" fill="var(--navy)" stroke="var(--red)" stroke-width="3"/><circle cx="21" cy="15" r="6" fill="none" stroke="#fff" stroke-width="2"/><path d="M18.5 15 l2 2 3-4" fill="none" stroke="#fff" stroke-width="1.6"/><path d="M9 25 h6 l5 2 h7 M9 29 h17 l5-5" fill="none" stroke="#fff" stroke-width="2" stroke-linecap="round"/></svg>
    <div class="benefit__title">GUARANTEED<br>PAYOUT*</div>
    <div class="benefit__text">Minimum $500 or 10% of<br>Total Invoice Paid Fast</div>
  </div>
  <div class="divider abs" style="left:190px"></div>
  <div class="benefit abs" style="left:190px">
    <svg class="benefit__icon" viewBox="0 0 40 40" aria-hidden="true"><circle cx="20" cy="20" r="18" fill="var(--navy)" stroke="var(--red)" stroke-width="3"/><rect x="11" y="10" width="12" height="18" rx="1" fill="none" stroke="#fff" stroke-width="2"/><path d="M14 15 h6 M14 19 h6 M14 23 h4" stroke="#fff" stroke-width="1.5"/><rect x="21" y="18" width="9" height="12" rx="1" fill="#fff"/><path d="M23 22 h5 M23 25 h5 M23 28 h5" stroke="var(--navy)" stroke-width="1.3"/></svg>
    <div class="benefit__title">FREE<br>ESTIMATES</div>
    <div class="benefit__text">Fast &amp; Free Inspections &amp;<br>Written Estimates</div>
  </div>
  <div class="divider abs" style="left:344px"></div>
  <div class="benefit abs" style="left:349px">
    <svg class="benefit__icon" viewBox="0 0 40 40" aria-hidden="true"><circle cx="20" cy="20" r="18" fill="var(--navy)" stroke="var(--red)" stroke-width="3"/><circle cx="20" cy="17" r="7" fill="none" stroke="#fff" stroke-width="2"/><path d="M17 17 l2 2 4-4" fill="none" stroke="#fff" stroke-width="1.6"/><path d="M16.5 26 h7 M17.5 29 h5" stroke="#fff" stroke-width="2" stroke-linecap="round"/><path d="M9 17 h2 M29 17 h2 M12 9 l1.5 1.5 M28 9 l-1.5 1.5" stroke="#fff" stroke-width="1.5"/></svg>
    <div class="benefit__title">AFFORDABLE<br>SOLUTIONS</div>
    <div class="benefit__text">Lowest Out of Pocket<br>Costs for Your Customers</div>
  </div>
  <div class="divider abs" style="left:498px"></div>
  <div class="benefit abs" style="left:510px">
    <svg class="benefit__icon" viewBox="0 0 40 40" aria-hidden="true"><circle cx="20" cy="20" r="18" fill="var(--navy)" stroke="var(--red)" stroke-width="3"/><path d="M15 9 l2.5 2.5 2.5-3 2.5 3 2.5-2.5 v4 h-10 z" fill="#fff"/><circle cx="20" cy="18" r="3" fill="#fff"/><circle cx="12.5" cy="21" r="2.5" fill="#fff"/><circle cx="27.5" cy="21" r="2.5" fill="#fff"/><path d="M14.5 29 a5.5 5 0 0 1 11 0 z M8 29 a4.5 4 0 0 1 7-3.5 M32 29 a4.5 4 0 0 0 -7-3.5" fill="#fff"/></svg>
    <div class="benefit__title">INDUSTRY<br>LEADERS</div>
    <div class="benefit__text">Licensed &amp; Certified Experts<br>Provide 100% Guarantee</div>
  </div>

  <footer class="contact abs" style="top:402px;height:48px">
    <div class="contact__call abs"><span class="contact__call-text">CALL, TEXT OR BOOK ONLINE</span></div>
    <div class="contact__info abs"></div>
    <span class="contact__phone">858-471-6093</span>
    <span class="contact__sep" style="top:10px;height:28px"></span>
    <span class="contact__web">www.BrightlaneRenovate.com</span>
  </footer>
</section>

<section class="flyer flyer--back">
  <div class="refer-panel abs">
    <svg width="266" height="198" viewBox="0 0 266 198" aria-hidden="true"><polygon points="66,198 118,175 118,18 200,18 266,62 266,198" fill="var(--shadow-blue)"/></svg>
    <div class="refer-title">
      <span class="lead" style="top:12px">THE MORE YOU</span>
      <span class="big refer">REFER</span>
      <span class="lead" style="top:95px">THE MORE YOU</span>
      <span class="big earn">EARN</span>
    </div>
  </div>
  <div class="cashflow-photo abs" role="img" aria-label="Photo of scattered hundred-dollar bills with letter tiles spelling CASH FLOW"></div>

  <div class="yellow-rule abs" style="top:198px"></div>
  <div class="tab tab--how abs">HOW IT WORKS</div>

  <div class="red-band abs"><div class="red-band__text">REFER : FLOOD, MOLD &amp; CONSTRUCTION JOBS</div></div>

  <article class="step abs" style="left:30px">
    <div class="step__photo step__photo--fans" role="img" aria-label="Photo of drying fans and dehumidifiers in a water-damaged room"></div>
    <h3 class="step__label">REFER FLOOD, MOLD<br>&amp; CONSTRUCTION JOBS :</h3>
    <p class="step__text">It’s Simple to Refer 24/7:Call,<br>Text or Book Online.</p>
  </article>
  <article class="step abs" style="left:246px">
    <div class="step__photo step__photo--estimate" role="img" aria-label="Photo of an estimator holding a clipboard in front of a house"></div>
    <h3 class="step__label">WE TAKE CARE OF<br>EVERYTHING:</h3>
    <p class="step__text">We Schedule a Free Estimate.<br>If Approved, You Get Paid.</p>
  </article>
  <article class="step abs" style="left:462px">
    <div class="step__photo step__photo--sign" role="img" aria-label="Photo of a yellow road sign reading get paid to share against a blue sky"></div>
    <h3 class="step__label">EVERYBODY BENEFITS<br>FROM REFERRALS</h3>
    <p class="step__text">We Provide Expert Quality<br>Work for Affordable Price.</p>
  </article>

  <footer class="contact abs" style="top:404px;height:46px">
    <div class="contact__call abs"><span class="contact__call-text">CALL, TEXT OR BOOK ONLINE</span></div>
    <div class="contact__info abs"></div>
    <span class="contact__phone">858-471-6093</span>
    <span class="contact__sep" style="top:9px;height:28px"></span>
    <span class="contact__web">www.BrightlaneRenovate.com</span>
  </footer>
</section>

</body>
</html>
```